KBT Business Cards

We require business cards for our business. We would like a matte black back to the card, with our logo centred in the middle. The front side of the card is open to design.

Target Market(s)

Clients looking for legal services (professional)

Industry/Entity Type

Legal

Contact Information for Business Card

Doran Kelbrath
Partner
Mobile: 0461 738 524
Email: doran@kbtlaw.co
Website: www.kbtlaw.co
Level 3, 118 Wendmore Street
Sydney NSW 2000

Font styles to use
Other font styles liked:
• Avenir

Colors
f04a50
ffffff
1b1b1b

Requirements
Must have
• Black back with logo included in the centre of the card.
• Our font is Avenir.

```html
<!DOCTYPE html>
<html lang="en">
<head>
<meta charset="utf-8">
<title>KBT Business Cards</title>
<link href="https://fonts.googleapis.com/css2?family=Lato:wght@400;700;900&display=swap" rel="stylesheet">
<style>
  :root {
    --accent: #f04a50;
    --ink: #1b1b1b;
    --ink-soft: #262626;
    --paper: #fcf8f8;
    --muted: #8a8a8a;
    --stage: #d9d9dc;
    --white: #ffffff;
  }
  * { box-sizing: border-box; margin: 0; padding: 0; }
  html, body { width: 1200px; height: 782px; overflow: hidden; }
  body {
    background: var(--stage);
    font-family: "Lato", Arial, sans-serif;
    color: var(--ink);
    position: relative;
  }
  .card {
    position: absolute;
    width: 540px;
    height: 328px;
    border-radius: 2px;
    overflow: hidden;
    box-shadow: 0 6px 18px rgba(0,0,0,0.18);
  }

  /* Back: matte black with centred mark */
  .card-back {
    left: 600px;
    top: 60px;
    background: var(--ink);
  }
  .card-back .pattern-field {
    position: absolute;
    inset: 0;
    background: linear-gradient(160deg, var(--ink-soft) 0%, var(--ink) 100%);
  }
  .card-back .back-mark {
    position: absolute;
    left: 50%;
    top: 50%;
    transform: translate(-50%, -50%);
    display: flex;
    align-items: center;
    gap: 10px;
    color: var(--white);
    font-weight: 900;
    font-size: 34px;
    line-height: 1;
    letter-spacing: 2px;
  }
  .back-mark .mark-square {
    width: 18px; height: 18px; background: var(--accent);
  }

  /* Front */
  .card-front {
    left: 60px;
    top: 394px;
    background: var(--paper);
  }
  .brand {
    position: absolute;
    left: 44px;
    top: 96px;
    display: flex;
    align-items: flex-start;
    gap: 14px;
  }
  .brand .mark-square {
    width: 30px; height: 30px;
    background: var(--accent);
    margin-top: 4px;
  }
  .brand-name {
    font-weight: 900;
    font-size: 22px;
    line-height: 21px;
    text-transform: uppercase;
    color: var(--ink);
    letter-spacing: 0.5px;
  }
  .divider {
    position: absolute;
    left: 262px;
    top: 90px;
    width: 1px;
    height: 120px;
    background: var(--muted);
  }
  .contact {
    position: absolute;
    left: 278px;
    top: 88px;
    font-size: 15px;
    line-height: 19px;
  }
  .contact .person {
    color: var(--accent);
    font-weight: 900;
    font-size: 18px;
    text-transform: uppercase;
    letter-spacing: 0.5px;
    line-height: 20px;
  }
  .contact .role { margin-bottom: 2px; }
  .contact .line { display: flex; align-items: center; gap: 7px; }
  .contact .line svg { width: 11px; height: 11px; flex: none; }
  .contact .address { margin-top: 1px; }
  .edge-bands {
    position: absolute;
    left: 0;
    bottom: 0;
    width: 540px;
    height: 56px;
  }
</style>
</head>
<body>

  <section class="card card-back" aria-label="Card back">
    <div class="pattern-field" role="img" aria-label="Matte black card surface"></div>
    <div class="back-mark">
      <span class="mark-square"></span>
      <span class="mark-name">KBT</span>
    </div>
  </section>

  <section class="card card-front" aria-label="Card front">
    <div class="brand">
      <span class="mark-square"></span>
      <div class="brand-name">Tarrant<br>Kelbrath<br>Legal</div>
    </div>

    <div class="divider"></div>

    <div class="contact">
      <div class="person">Doran Kelbrath</div>
      <div class="role">Partner</div>
      <div class="line">
        <svg viewBox="0 0 12 12" aria-hidden="true"><path fill="var(--accent)" d="M2.5 1h2l1 2.5-1.3 1a6 6 0 0 0 3.3 3.3l1-1.3 2.5 1v2a1 1 0 0 1-1 1A9 9 0 0 1 1.5 2a1 1 0 0 1 1-1z"/></svg>
        <span>0461 738 524</span>
      </div>
      <div class="line">
        <svg viewBox="0 0 12 12" aria-hidden="true"><rect x="0.5" y="2" width="11" height="8" fill="var(--accent)"/><path d="M0.8 2.4 6 6.6l5.2-4.2" fill="none" stroke="var(--paper)" stroke-width="1"/></svg>
        <span>doran@kbtlaw.co</span>
      </div>
      <div class="line">
        <svg viewBox="0 0 12 12" aria-hidden="true"><circle cx="6" cy="6" r="5.5" fill="var(--accent)"/><path d="M0.5 6h11M6 0.5c-2.4 3-2.4 8 0 11M6 0.5c2.4 3 2.4 8 0 11" fill="none" stroke="var(--paper)" stroke-width="0.8"/></svg>
        <span>www.kbtlaw.co</span>
      </div>
      <div class="address">Level 3, 118 Wendmore<br>Street, Sydney NSW 2000</div>
    </div>

    <svg class="edge-bands" viewBox="0 0 540 56" aria-hidden="true">
      <polygon points="0,18 300,18 287,38 0,38" fill="var(--accent)"/>
      <polygon points="306,18 540,40 540,56 0,56 0,38 292,38" fill="var(--ink)"/>
    </svg>
  </section>

</body>
</html>
```